Refresh of far from plain IT company website

Our web site is starting to show it's age. You can see the existing site here: www.plumbwick.net. As a growing company we want to come across as a dynamic collection of IT experts.

We want to update the design so are open to any colour palette and look, but want to retain our current table logo. We use the logo on our business cards but with a white background - see the attached file, so you don't need to keep the brown or the green.

The design should consider the range of browsers that will be looking at the site - so please show how it will look on a wide screen laptop and a 768x1024 tablet.

We want to add some pages about our team and their skills, probably with photos of each person on the team.

This is an uncoded project - the PSD files of the design is required, not coding.
Updates

Thanks everyone for the submissions so far.  It's a holiday day in the UK today but we will get some feedback on the designs so far out to you.

Target Market(s)

Architects and other creative types looking for IT support

Industry/Entity Type

Business

Font styles to use
Serif
Sans Serif

Requirements
Must have
• Must look good on a laptop and an iPad.

```html
<!DOCTYPE html>
<html lang="en">
<head>
<meta charset="utf-8">
<title>Plumbwick – Serious IT Support for Business</title>
<link href="https://fonts.googleapis.com/css2?family=Noto+Sans:wght@400;700&family=Roboto:wght@700;900&display=swap" rel="stylesheet">
<style>
:root{
  --plum:#8f1a57;
  --plum-dark:#6f1242;
  --gold:#d9a816;
  --ink:#333333;
  --text:#8a8a8a;
  --grey-band:#efefef;
  --pattern:#f4f4f4;
  --line:#dddddd;
  --footer:#2d2d2d;
  --white:#ffffff;
}
*{box-sizing:border-box;margin:0;padding:0}
html,body{width:1200px;height:2452px;overflow:hidden;background:var(--white)}
body{position:relative;font-family:"Noto Sans",sans-serif;color:var(--ink)}
.abs{position:absolute}
.top-strip{left:0;top:0;width:1200px;height:10px;background:var(--plum)}

/* header */
.brand{left:82px;top:70px;display:flex;align-items:center;gap:22px}
.brand-mark{width:62px;height:42px;background:var(--gold)}
.brand-name{font-size:44px;font-weight:700;color:var(--plum);letter-spacing:-0.5px}
.social{display:flex;gap:8px}
.social span{width:27px;height:27px;border-radius:50%;display:block}
.header-social{left:1002px;top:44px}
.header-social span:nth-child(1){background:#3d8fcf}
.header-social span:nth-child(2){background:#3b5a9a}
.header-social span:nth-child(3){background:#1f7bb4}
.header-social span:nth-child(4){background:#e58a2b}
.callus{left:972px;top:96px;display:flex;gap:14px;align-items:center}
.callus-icon{width:36px;height:34px;background:var(--plum);border-radius:4px;display:flex;align-items:center;justify-content:center}
.callus-text{font-size:15px;line-height:21px;color:var(--ink)}
.callus-text b{display:block;font-weight:400;color:var(--plum)}

/* nav */
.nav{left:57px;top:150px;width:1088px;height:54px;background:linear-gradient(#505050,#2a2a2a);border-bottom:4px solid var(--plum);display:flex;align-items:center;padding-left:8px}
.nav a{color:#eee;text-decoration:none;font-size:16px;padding:0 25px;height:50px;line-height:50px;border-right:1px solid #555;position:relative}
.nav a:last-of-type{border-right:none}
.nav a.active::after{content:"";position:absolute;left:50%;bottom:0;margin-left:-6px;border:6px solid transparent;border-bottom-color:var(--plum)}
.search{position:absolute;left:863px;top:13px;width:208px;height:27px;border-radius:14px;background:#fff;font-size:13px;color:#999;padding:5px 12px}
.search svg{position:absolute;right:10px;top:7px}

/* hero */
.pattern-band{left:0;top:561px;width:1200px;height:518px;background:var(--pattern);border-top:1px solid var(--line);border-bottom:1px solid var(--line)}
.hero{left:57px;top:216px;width:1088px;height:430px;background:linear-gradient(180deg,#ede1cf 0%,#e7cfa6 40%,#b9a08a 62%,#a58f82 100%);border-bottom:5px solid #333}
.hero-title{left:128px;top:306px;font-family:"Roboto",sans-serif;font-weight:900;line-height:1}
.hero-title .t1{font-size:34px;color:var(--plum);letter-spacing:1.5px}
.hero-title .t2{font-size:50px;color:#222;letter-spacing:2px;margin-top:6px}
.hero-note{left:57px;top:392px;width:471px;height:110px;background:rgba(217,168,22,.92);color:#fff;font-size:15px;line-height:21px;padding:14px 20px 0 74px}

/* welcome */
.welcome{left:72px;top:714px;width:634px}
.section-title{font-size:19px;letter-spacing:1.5px;color:var(--ink);font-weight:400}
.section-title em{font-style:normal;color:var(--plum)}
.welcome .section-title{padding-bottom:14px;border-bottom:1px solid #ccc}
.welcome p{font-size:15.5px;line-height:23px;color:var(--text);margin-top:20px;width:660px;height:auto}
.btn{display:flex;align-items:center;justify-content:center;gap:14px;color:#fff;font-size:16px;background:linear-gradient(#555,#1e1e1e)}
.readmore{left:74px;top:974px;width:166px;height:46px;border-bottom:4px solid var(--plum);border-radius:3px}

/* quote */
.quote{left:814px;top:692px;width:316px;height:299px;background:#e8e8e8;border:1px solid #d5d5d5;border-radius:3px;box-shadow:0 2px 4px rgba(0,0,0,.15)}
.quote-head{height:40px;background:var(--plum);color:#fff;font-size:16px;letter-spacing:1px;padding:10px 20px;display:flex;justify-content:space-between;align-items:center}
.field{position:absolute;background:#fff;border:1px solid #ccc;border-radius:2px;font-size:14px;color:#888;padding:6px 10px}
.qbtn{position:absolute;top:228px;height:32px;width:144px;font-size:15px;letter-spacing:1px;display:flex;align-items:center;justify-content:center;color:#fff}
.qsend{left:9px;background:linear-gradient(#444,#1e1e1e)}
.qreset{left:159px;background:linear-gradient(#999,#777)}

/* services */
.services-head{left:0;top:1140px;width:1200px;text-align:center}
.services-intro{left:160px;top:1198px;width:880px;text-align:center;font-size:15.5px;line-height:24px;color:var(--text)}
.service{width:300px}
.service .icon{position:absolute;left:-3px;top:0;width:68px;height:68px;border:1px solid #bbb;border-radius:50%;display:flex;align-items:center;justify-content:center}
.service h3{margin-left:93px;font-size:21px;font-weight:400;color:var(--plum);line-height:26px}
.service p{margin-left:93px;font-size:14.5px;line-height:20px;color:#555;margin-top:6px;width:230px}
.contact{left:482px;top:1730px;width:244px;height:47px;border-radius:24px;box-shadow:0 3px 5px rgba(0,0,0,.3)}

/* partners */
.partners{left:0;top:1861px;width:1200px;height:170px;background:var(--grey-band)}
.badge{position:absolute;background:#8c8c8c}

/* footer */
.footer{left:0;top:2031px;width:1200px;height:381px;background:var(--footer)}
.foot-col{color:#fff}
.foot-col h4{font-size:16px;font-weight:400;letter-spacing:1.5px;padding-bottom:14px;border-bottom:1px solid #555}
.foot-links{list-style:none;font-size:13.5px;line-height:24px;color:#eee;margin-top:12px}
.map{left:136px;top:2155px;width:273px;height:219px;background:linear-gradient(135deg,#d9d3a8,#c7d6b9 45%,#b8c7dd);border:3px solid #ddd}
.footer-social span{background:#fff;width:25px;height:25px}
.copyright{left:0;top:2412px;width:1200px;height:40px;background:var(--plum);color:#fff;font-size:13px;text-align:center;line-height:40px}
</style>
</head>
<body>
<div class="abs top-strip"></div>

<header>
  <div class="abs brand"><span class="brand-mark"></span><span class="brand-name">plumbwick</span></div>
  <div class="abs social header-social"><span></span><span></span><span></span><span></span></div>
  <div class="abs callus">
    <div class="callus-icon"><svg width="22" height="18" viewBox="0 0 22 18"><path d="M2 6c0-3 4-4 9-4s9 1 9 4v2h-5V6H7v2H2z" fill="#fff"/><rect x="4" y="9" width="14" height="8" rx="2" fill="#fff"/><circle cx="11" cy="13" r="2" fill="#8f1a57"/></svg></div>
    <div class="callus-text">Call us today<b>020 7946 0182</b></div>
  </div>
  <nav class="abs nav">
    <a class="active">Home</a><a>About us</a><a>What we do</a><a>News blog</a><a>Articles</a><a>Clients</a><a>Partners</a>
    <div class="search">Keyword Search...<svg width="12" height="12" viewBox="0 0 12 12"><circle cx="5" cy="5" r="3.5" stroke="#888" stroke-width="1.5" fill="none"/><path d="M8 8l3 3" stroke="#888" stroke-width="1.5"/></svg></div>
  </nav>
</header>

<div class="abs pattern-band"></div>
<div class="abs hero" role="img" aria-label="Photo of a businessman working on a laptop on a wooden pier by the sea at dusk, with letters floating from the screen"></div>
<div class="abs hero-title"><div class="t1">SERIOUS IT SUPPORT</div><div class="t2">FOR BUSINESS</div></div>
<div class="abs hero-note">Lorem ipsum dolor sit amet, consectetur adipiscing elit. Nam dapibus blandit enim, eget pellentesque nibh ullamcorper id. Morbi luctus porta arcu sed.consectetur adipiscing elit nibh ullamcorper.</div>

<section class="abs welcome">
  <h2 class="section-title">WELCOME TO <em>PLUMBWICK</em></h2>
  <p>Plumbwick was established with a specific aim: to consistently deliver an advanced and comprehensive IT service for ambitious growing companies across many industry sectors. We aim to provide the very best in service and support, and to aid business growth through the effective and skilled use of modern IT solutions.</p>
  <p>Founded in 2003, we have grown rapidly and have delivered successful business solutions to small and medium sized businesses, working with customers across a wide IT spectrum. The knowledge, experience and expertise which we have gained</p>
</section>
<a class="abs btn readmore">Read more <svg width="18" height="18" viewBox="0 0 18 18"><circle cx="9" cy="9" r="8" fill="#fff"/><path d="M5 9h6M9 6l3 3-3 3" stroke="#222" stroke-width="2" fill="none"/></svg></a>

<form class="abs quote">
  <div class="quote-head">GET A FREE QUOTE <svg width="30" height="20" viewBox="0 0 30 20"><rect x="1" y="1" width="28" height="18" fill="none" stroke="#fff" stroke-width="1.5"/><path d="M1 1l14 10L29 1" fill="none" stroke="#fff" stroke-width="1.5"/></svg></div>
  <div class="field" style="left:9px;top:56px;width:143px;height:33px">Firstname</div>
  <div class="field" style="left:159px;top:56px;width:144px;height:33px">Email</div>
  <div class="field" style="left:9px;top:105px;width:294px;height:104px">Message</div>
  <div class="qbtn qsend">SEND QUOTE</div>
  <div class="qbtn qreset">RESET FORM</div>
</form>

<h2 class="abs section-title services-head">WHAT <em>WE CAN DO</em> FOR YOU</h2>
<p class="abs services-intro">Plumbwick offer a wide range of services tailored to meet our client's business needs. We aim to deliver world-class support and strategic advice backed-up by an effective on-site presence. Our core business is focussed on construction professionals and creative companies with sophisticated and fast-changing IT requirements.</p>

<div class="abs service" style="left:97px;top:1344px"><div class="icon"><svg width="36" height="36" viewBox="0 0 36 36"><circle cx="18" cy="18" r="15" fill="#333"/><circle cx="18" cy="18" r="6" fill="#fff"/></svg></div><h3>Support</h3><p>Plumbwick's clients enjoy regular scheduled on-site visits from an engineer.</p></div>
<div class="abs service" style="left:448px;top:1344px"><div class="icon"><svg width="32" height="32" viewBox="0 0 32 32"><rect x="4" y="10" width="24" height="18" fill="#333"/><circle cx="16" cy="9" r="5" fill="#333"/></svg></div><h3>Consultancy</h3><p>Plumbwick firmly believe that business requirements must be the primary driver for IT strategy.</p></div>
<div class="abs service" style="left:797px;top:1344px"><div class="icon"><svg width="34" height="34" viewBox="0 0 34 34"><circle cx="17" cy="17" r="11" fill="none" stroke="#333" stroke-width="6" stroke-dasharray="5 3"/><circle cx="17" cy="17" r="4" fill="#333"/></svg></div><h3>CAD</h3><p>A large number of Plumbwick's clients are users of Corvel Draftline CAD software.</p></div>
<div class="abs service" style="left:97px;top:1541px"><div class="icon"><svg width="26" height="34" viewBox="0 0 26 34"><rect x="5" y="2" width="16" height="26" fill="#333"/><rect x="2" y="29" width="22" height="3" fill="#333"/></svg></div><h3>Hosting</h3><p>Plumbwick have expertise in designing the architecture of highly available, highly scalable web sites.</p></div>
<div class="abs service" style="left:448px;top:1541px"><div class="icon"><svg width="32" height="32" viewBox="0 0 32 32"><path d="M5 5l22 22M27 5L5 27" stroke="#333" stroke-width="5"/></svg></div><h3>Development</h3><p>Our in-house development team build bespoke software solutions, tailored to the specific needs of our clients.</p></div>
<div class="abs service" style="left:797px;top:1541px"><div class="icon"><svg width="32" height="32" viewBox="0 0 32 32"><ellipse cx="13" cy="8" rx="9" ry="4" fill="#333"/><rect x="4" y="10" width="18" height="14" fill="#333"/><circle cx="23" cy="23" r="7" fill="#333" stroke="#fff" stroke-width="2"/><path d="M23 19v8M19 23h8" stroke="#fff" stroke-width="2"/></svg></div><h3>Other Services</h3><p>Plumbwick's clients enjoy regular scheduled on-site visits from an engineer.</p></div>

<a class="abs btn contact">Contact us today <svg width="20" height="20" viewBox="0 0 18 18"><circle cx="9" cy="9" r="8" fill="#fff"/><path d="M5 9h6M9 6l3 3-3 3" stroke="#222" stroke-width="2" fill="none"/></svg></a>

<section class="abs partners" aria-label="Partners">
  <span class="badge" style="left:115px;top:55px;width:115px;height:62px;border-radius:50%"></span>
  <span class="badge" style="left:282px;top:67px;width:162px;height:38px;border-radius:19px"></span>
  <span class="badge" style="left:524px;top:74px;width:130px;height:24px"></span>
  <span class="badge" style="left:718px;top:75px;width:155px;height:22px"></span>
  <span class="badge" style="left:957px;top:46px;width:80px;height:80px;border-radius:50%"></span>
</section>

<footer class="abs footer"></footer>
<div class="abs foot-col" style="left:132px;top:2098px;width:284px"><h4>LOCATION MAP</h4></div>
<div class="abs map" role="img" aria-label="Street map showing the office location with map pins"></div>
<div class="abs foot-col" style="left:504px;top:2098px;width:246px">
  <h4>QUICKLINKS</h4>
  <div style="display:flex;gap:80px;padding-left:6px">
    <ul class="foot-links"><li>Home</li><li>About us</li><li>What we do</li><li>News blog</li></ul>
    <ul class="foot-links"><li>Articles</li><li>Clients</li><li>Partners</li></ul>
  </div>
</div>
<div class="abs foot-col" style="left:844px;top:2098px;width:212px">
  <h4>USEFUL INFORMATION</h4>
  <ul class="foot-links" style="padding-left:6px"><li>Sitemap</li><li>F.A.Q</li><li>Privacy Policy</li><li>Terms &amp; Conditions</li></ul>
  <div class="social footer-social" style="margin:14px 0 0 8px;gap:6px"><span></span><span></span><span></span><span></span></div>
</div>
<div class="abs copyright">Plumbwick Copyright 2014 &nbsp;All rights reserved</div>
</body>
</html>
```